New Bag and Tote Design Project

colour green and gold
informaiton for the bag.
white colour with clear window.  

Information on the bag   100% Australia Product Must have Sunfield Harvest Symble  Nutrition Information Serving Size: 1 bag 50g Serving per bag : 2bag  
Ingredient : 100% Australian Grown and Pack Gluten Fee
Product of Australia  

Information: Australian Mangoes has a distinctive sweet aroma. Its tast so good that people forget they are also extemly healthy.  The high level of fiber, pectin, VitaminC help to lower serium cholesterol levels. a decrease rick of colon cancer, improvement in digestion and bone health and event benefit for the skin and hair. with the dehydrate method of processing let you get an all natural taste.

Ingredient 100% Australian Grown Mangos

Target Market(s)

Super market shelves, young mum, health focus.

Industry/Entity Type

Product

Colors
fbee34
9bcb3c

Requirements
Must have
• Company logo and Australian product logo.
• Sample from other company.
• Australian Dried Mangoes.
• Sunfield Harvest logo
Nice to have
• Australian colour, mangoes picture
• Friendly sign

```html
<!DOCTYPE html>
<html lang="en">
<head>
<meta charset="utf-8">
<title>Australian Dried Mangoes – Bag</title>
<link href="https://fonts.googleapis.com/css2?family=Open+Sans:wght@400;600;700;800&family=Archivo+Narrow:wght@400;700&display=swap" rel="stylesheet">
<style>
  :root{
    --green:#7ab52f;
    --green-light:#9bcb3c;
    --green-dark:#4f8a1e;
    --gold:#fbee34;
    --orange:#f08c1e;
    --white:#ffffff;
    --ink:#111111;
    --backdrop:#efefec;
  }
  *{box-sizing:border-box;margin:0;padding:0}
  html,body{width:1200px;height:1200px;overflow:hidden;background:var(--backdrop)}
  body{position:relative;font-family:"Open Sans",Arial,sans-serif}
  .bag{position:absolute;top:210px;width:444px;height:756px;background:var(--white);overflow:hidden;box-shadow:0 4px 14px rgba(0,0,0,.18)}
  .bag--front{left:120px}
  .bag--back{left:630px}
  .bag__shapes{position:absolute;inset:0;width:100%;height:100%}
  .abs{position:absolute}

  /* front */
  .kids{left:18px;top:14px;width:118px;color:var(--white);font-weight:800;font-size:10px;line-height:1.1}
  .kids__label{display:block;text-align:center}
  .kids__row{display:flex;align-items:center;gap:6px;margin-top:3px}
  .kids__art{flex:none;display:block;width:60px;height:30px;border-radius:15px;background:linear-gradient(90deg,#a6d45a,#8fc447)}
  .kids__age{text-align:left}
  .brand{display:flex;align-items:center;gap:6px;color:var(--green-dark);font-weight:700;font-size:12px;line-height:1.1}
  .brand__dot{width:34px;height:34px;border-radius:50%;background:var(--green)}
  .front-brand{left:282px;top:104px}
  .title{left:0;width:444px;text-align:center;color:var(--green)}
  .title__small{top:196px;font-weight:800;font-size:27px}
  .title__big{top:220px;font-weight:800;font-size:45px;letter-spacing:-1px;color:var(--green-dark)}
  .title__big span{color:var(--green-light)}
  .title__sub{top:276px;font-weight:700;font-size:13px;color:var(--green)}
  .blurb{left:48px;top:300px;width:348px;text-align:center;font-size:8.2px;line-height:1.45;font-weight:600;text-transform:uppercase;color:var(--green)}
  .mango-photo{left:172px;top:438px;width:250px;height:236px;border-radius:46% 40% 38% 44%;background:radial-gradient(circle at 62% 46%,#f7b21c 0,#f5c52a 40%,#f2de4a 70%,rgba(242,222,74,0) 72%)}
  .packed{left:22px;top:530px;width:150px;color:var(--green-dark);font-weight:700;font-size:11.5px;line-height:1.25;text-align:center}
  .count{left:24px;top:628px;width:54px;height:54px;border-radius:50%;background:var(--orange);color:var(--white);font-weight:800;font-size:18px;display:flex;align-items:center;justify-content:center}
  .count-label{left:84px;top:650px;color:var(--white);font-weight:700;font-size:14px;line-height:1.05}
  .serving{left:22px;top:724px;color:var(--white);font-weight:700;font-size:11px}
  .gluten{left:362px;top:672px;width:62px;height:62px;border-radius:50%;background:var(--orange);border:3px dotted var(--white);color:var(--white);font-weight:800;font-size:12px;line-height:1;display:flex;align-items:center;justify-content:center;text-align:center}
  .ingredient-front{left:150px;top:712px;width:200px;text-align:center;color:var(--green-dark);font-weight:700;font-size:8.5px;line-height:1.25}

  /* back */
  .nutrition{left:20px;top:154px;width:172px;height:398px;background:var(--green);padding:4px}
  .nf{width:100%;height:100%;background:var(--white);border:1px solid var(--ink);padding:3px 5px;font-family:"Archivo Narrow",Arial,sans-serif;color:var(--ink);font-size:7.6px;line-height:1.3}
  .nf__title{font-weight:700;font-size:19px;line-height:1;letter-spacing:-.3px}
  .nf__rule{border-top:1px solid var(--ink)}
  .nf__rule--thick{border-top:5px solid var(--ink)}
  .nf__rule--mid{border-top:3px solid var(--ink)}
  .nf__row{display:flex;justify-content:space-between;border-top:1px solid #555}
  .nf__row b{font-weight:700}
  .nf__row--indent{padding-left:8px}
  .nf__note{font-size:6px;line-height:1.25;padding-top:2px}
  .nf__grid{display:grid;grid-template-columns:1.6fr 1fr .7fr .7fr;font-size:5.8px;line-height:1.25}
  .ingredient-back{left:210px;top:154px;color:var(--green);font-weight:700;font-size:10px;line-height:1.5}
  .benefits{left:210px;top:222px;list-style:none;color:var(--orange);font-weight:700;font-size:10px}
  .benefits li{display:flex;align-items:center;gap:10px;height:30px}
  .benefits li::before{content:"";width:13px;height:18px;border-radius:50% 50% 50% 50%/60% 60% 40% 40%;background:var(--orange)}
  .mascot{left:204px;top:386px;width:162px;height:214px;border-radius:48% 48% 44% 44%;background:radial-gradient(circle at 45% 40%,#fbee34,#f5c52a 60%,#e9a91a)}
  .back-brand{left:36px;top:566px}
  .origin-badge{left:46px;top:626px;width:114px;height:50px;border:2px solid var(--green-dark);border-radius:4px;display:flex;align-items:center;gap:6px;padding:0 6px;color:var(--green-dark);font-weight:700;font-size:11px;line-height:1.1}
  .origin-badge__mark{flex:none;width:26px;height:26px;background:var(--green)}
  .packed-back{right:28px;top:696px;text-align:right;color:var(--white);font-weight:700;font-size:13px;line-height:1.3}
</style>
</head>
<body>

<section class="bag bag--front" aria-label="Front of bag">
  <svg class="bag__shapes" viewBox="0 0 444 756" preserveAspectRatio="none" aria-hidden="true">
    <path d="M0 0H444V70Q240 86 0 152Z" fill="var(--green)"/>
    <path d="M0 152Q240 86 444 70" fill="none" stroke="var(--gold)" stroke-width="3"/>
    <path d="M0 566Q200 640 444 656V756H0Z" fill="var(--green)"/>
    <path d="M36 518V400Q180 376 326 384Q296 508 36 518Z" fill="none" stroke="var(--green-light)" stroke-width="3"/>
  </svg>

  <div class="abs kids">
    <span class="kids__label">SUITABLE FOR KIDS</span>
    <div class="kids__row">
      <span class="kids__art" role="img" aria-label="Two smiling children illustration"></span>
      <span class="kids__age">FROM<br>12 MONTHS</span>
    </div>
  </div>

  <div class="abs brand front-brand"><span class="brand__dot"></span>GOLDLEAF<br>ORCHARDS</div>

  <h1 class="abs title title__small">AUSTRALIAN</h1>
  <p class="abs title title__big"><span>DRIED</span>MANGOES</p>
  <p class="abs title title__sub">100% AUSTRALIA PRODUCT</p>

  <p class="abs blurb">Australian mangoes has a distinctive sweet aroma. Its tast so good that people forget they are also extemly healthy. The high level of fiber, pectin, vitaminC help to lower serium cholesterol levels. A decrease rick of colon cancer, improvement in digestion and bone health and event benefit for the skin and hair. With the dehydrat method of processing let you get an all natural taste.</p>

  <div class="abs mango-photo" role="img" aria-label="Photo of a whole mango and a cubed mango half"></div>

  <p class="abs packed">Grow and packed<br>by Brightvale Growers.</p>

  <div class="abs count">x2</div>
  <p class="abs count-label">Yummy<br>Bags</p>
  <p class="abs serving">Serving Size: 1 bag 50g</p>

  <div class="abs gluten">GLUTEN<br>FREE</div>
  <p class="abs ingredient-front">Ingredient : 100% Australian Grown<br>and Pack Gluten Fee</p>
</section>

<section class="bag bag--back" aria-label="Back of bag">
  <svg class="bag__shapes" viewBox="0 0 444 756" preserveAspectRatio="none" aria-hidden="true">
    <path d="M0 0H444V40Q220 44 0 92Z" fill="var(--green)"/>
    <path d="M0 92Q220 44 444 40" fill="none" stroke="var(--gold)" stroke-width="3"/>
    <path d="M0 756V730Q260 720 444 642V756Z" fill="var(--green)"/>
  </svg>

  <div class="abs nutrition">
    <div class="nf">
      <div class="nf__title">Nutrition Facts</div>
      <div>Serving Size: 1 cup, sliced (165g)</div>
      <div>Serving Per Container</div>
      <div class="nf__rule nf__rule--thick"></div>
      <div style="font-size:6px">Amount Per Serving</div>
      <div class="nf__row"><span><b>Calories:</b> 100</span><span>Calories from Fat: 5</span></div>
      <div class="nf__rule nf__rule--mid"></div>
      <div style="text-align:right"><b>% Daily Value*</b></div>
      <div class="nf__row"><span><b>Total Fat</b> 0.5g</span><b>1%</b></div>
      <div class="nf__row nf__row--indent"><span>Saturated Fat 0g</span><b>0%</b></div>
      <div class="nf__row nf__row--indent"><span>Trans Fat 0g</span><b>0%</b></div>
      <div class="nf__row"><span><b>Cholesterol</b> 0mg</span><b>0%</b></div>
      <div class="nf__row"><span><b>Sodium</b> 0mg</span><b>0%</b></div>
      <div class="nf__row"><span><b>Total Carbohydrate</b> 25g</span><b>8%</b></div>
      <div class="nf__row nf__row--indent"><span>Dietary Fiber 3g</span><b>12%</b></div>
      <div class="nf__row nf__row--indent"><span>Sugars 23g</span><span></span></div>
      <div class="nf__row"><span><b>Protein</b> 1g</span><span></span></div>
      <div class="nf__rule nf__rule--thick"></div>
      <div class="nf__row"><span>Vitamin A 35% •</span><span>Vitamin C 100%</span></div>
      <div class="nf__row"><span>Calcium 2% •</span><span>Iron 2%</span></div>
      <div class="nf__row"><span>Vitamin B6 10% •</span><span>Copper 10%</span></div>
      <div class="nf__row"><span>Folate 20% •</span><span>Vitamin K 8%</span></div>
      <div class="nf__row"><span>Potassium 8%</span><span></span></div>
      <div class="nf__rule"></div>
      <p class="nf__note">*Percent Daily Values are based on a 2,000 calorie diet. Your Daily Values may be higher or lower depending on your calorie needs:</p>
      <div class="nf__grid">
        <span></span><span>Calories</span><span>2,000</span><span>2,500</span>
        <span>Total Fat</span><span>Less Than</span><span>65g</span><span>80g</span>
        <span>&nbsp;Saturated Fat</span><span>Less Than</span><span>20g</span><span>25g</span>
        <span>Cholesterol</span><span>Less Than</span><span>300mg</span><span>300mg</span>
        <span>Sodium</span><span>Less Than</span><span>2,400mg</span><span>2,400mg</span>
        <span>Total Carbohydrate</span><span></span><span>300g</span><span>375g</span>
        <span>&nbsp;Dietary Fiber</span><span></span><span>25g</span><span>30g</span>
      </div>
      <div class="nf__rule"></div>
      <p class="nf__note">Calories Per Gram<br>Fat 9 • Carbohydrate 4 • Protein 4</p>
    </div>
  </div>

  <p class="abs ingredient-back">INGREDIENT:<br>100% Australian Grown<br>and Pack Gluten Fee</p>
  <ul class="abs benefits">
    <li>100% NATURAL</li>
    <li>THE HIGH LEVEL OF FIBER</li>
    <li>SWEET AROMA</li>
  </ul>

  <div class="abs mascot" role="img" aria-label="Friendly waving mango character illustration"></div>

  <div class="abs brand back-brand"><span class="brand__dot"></span>GOLDLEAF<br>ORCHARDS</div>
  <div class="abs origin-badge"><span class="origin-badge__mark"></span>Sunfield<br>Harvest</div>

  <p class="abs packed-back">Grow and packed<br>by Brightvale Growers.</p>
</section>

</body>
</html>
```